Online interactive tutorial for year 2 to year 12 students in Australia

Website design for a new online tutorial for year 2 to year 12 students in Australia.

- The tutorial will be conducted via live webcam and within a dedicated interactive space
- The tutorial will be provided by high scoring undergraduates studying in top Australian universities.
- The tutors will be going through interviews & assessments & only top students are allowed to apply.
- Parents will do search and select tutor and have short 15 mins video interaction with potential tutors before booking them for their children for tutoring.
- hourly cost of booking (no monthly subscription or no hour limits)
- Tutors will have their own profile

Please see the attached for detailed page functionality.

The look and feel of the design must consider the following:
- must be educational but not dull and should stand out
- must appeal to younger generation - tutees (8-18 years), tutors (19-25), parents (30-50).
- Ideas for Logos (brivora.com.au but not confirmed)

Target Market(s)

tutees (8-18 years), tutors (19-25 years), parents (30-50 years).

Industry/Entity Type

Education

Coding

Coded - Design and coding required

Number of Pages Required

5+ page

Font styles to use
Serif

Requirements
Must have
• The look and feel of the design must consider the following:
• - must be educational but not dull and should stand out
• - must appeal to younger generation - tutees (8-18 years), tutors (19-25), parents (30-50).
Should not have
• Dullness

```html
<!DOCTYPE html>
<html lang="en">
<head>
<meta charset="utf-8">
<title>Brivora — Online Training</title>
<link href="https://fonts.googleapis.com/css2?family=Lato:wght@300;400;700;900&family=Open+Sans:wght@400;600&display=swap" rel="stylesheet">
<style>
  :root {
    --sky: #29b6e8;
    --sky-dark: #1a9fd2;
    --lime: #8dc63f;
    --lime-dark: #76b02a;
    --ink: #333a40;
    --muted: #5c6368;
    --footer: #47535c;
    --footer-deep: #3c474f;
    --footer-field: #5a666e;
    --white: #ffffff;
  }
  * { box-sizing: border-box; margin: 0; padding: 0; }
  html, body { width: 1200px; height: 2486px; overflow: hidden; }
  body { position: relative; background: var(--white); font-family: "Open Sans", Arial, sans-serif; color: var(--ink); }
  .abs { position: absolute; }

  /* Top bar */
  .topbar { left: 0; top: 0; width: 1200px; height: 41px; background: var(--sky); color: var(--white); font-size: 11px; }
  .topbar .contact-item { top: 13px; display: flex; align-items: center; gap: 8px; }
  .topbar .social { right: 132px; top: 13px; display: flex; gap: 10px; }
  .topbar .social span { width: 10px; height: 10px; border-radius: 50%; background: var(--white); display: block; }

  /* Header */
  .header { left: 0; top: 41px; width: 1200px; height: 105px; background: var(--white); }
  .brand { left: 138px; top: 30px; display: flex; align-items: center; gap: 14px; }
  .brand-mark { width: 28px; height: 28px; background: var(--lime); }
  .brand-name { font-family: "Lato", Arial, sans-serif; font-weight: 700; font-size: 38px; color: var(--sky); line-height: 1; }
  .auth-btn { top: 17px; height: 28px; border-radius: 3px; color: var(--white); font-family: "Lato", Arial, sans-serif; font-size: 11px; letter-spacing: .5px; display: flex; align-items: center; justify-content: center; }
  .auth-register { left: 873px; width: 101px; background: var(--sky); }
  .auth-login { left: 979px; width: 86px; background: var(--lime); }
  .nav { top: 69px; left: 0; width: 1200px; font-family: "Lato", Arial, sans-serif; font-size: 12px; letter-spacing: .4px; color: var(--ink); }
  .nav a { position: absolute; color: inherit; text-decoration: none; }
  .nav a.active { color: var(--sky); }
  .nav .active-line { left: 580px; top: 100px; width: 50px; height: 3px; background: var(--sky); }

  /* Hero */
  .hero { left: 0; top: 146px; width: 1200px; height: 444px; background: linear-gradient(115deg, #6d7e8a 0%, #4d5f6d 40%, #5a5156 70%, #7a6a66 100%); }
  .hero-title { left: 0; top: 130px; width: 1200px; text-align: center; font-family: "Lato", Arial, sans-serif; font-weight: 700; font-size: 72px; color: var(--white); text-shadow: 0 3px 6px rgba(0,0,0,.45); }
  .hero-sub { left: 0; top: 243px; width: 1200px; text-align: center; font-size: 14px; color: var(--white); }
  .hero-btn { left: 540px; top: 298px; width: 120px; height: 42px; background: var(--sky); color: var(--white); border-radius: 3px; font-family: "Lato", Arial, sans-serif; font-size: 13px; font-weight: 700; display: flex; align-items: center; justify-content: center; }
  .hero-dots { left: 566px; top: 396px; display: flex; gap: 9px; }
  .hero-dots span { width: 16px; height: 16px; border-radius: 50%; background: var(--white); display: block; }
  .hero-dots span.current { background: var(--sky); border: 3px solid var(--white); }

  /* Welcome */
  .section-title { left: 0; width: 1200px; text-align: center; font-family: "Lato", Arial, sans-serif; font-weight: 700; color: var(--sky); }
  .welcome-title { top: 630px; font-size: 36px; }
  .welcome-intro { left: 133px; top: 688px; width: 936px; text-align: center; font-size: 11px; line-height: 19px; color: var(--muted); }
  .feature { top: 778px; width: 300px; text-align: center; }
  .feature-icon { width: 75px; height: 75px; border-radius: 50%; margin: 0 auto; display: flex; align-items: center; justify-content: center; }
  .feature-icon.green { background: var(--lime); }
  .feature-icon.blue { background: var(--sky); }
  .feature h3 { margin-top: 27px; font-family: "Lato", Arial, sans-serif; font-weight: 400; font-size: 19px; color: var(--ink); }
  .feature p { margin: 12px auto 0; width: 280px; font-size: 11.5px; line-height: 20px; color: var(--muted); }
  .btn-small { margin: 20px auto 0; width: 91px; height: 31px; border-radius: 3px; background: var(--sky); color: var(--white); font-size: 11px; display: flex; align-items: center; justify-content: center; }

  /* How it works */
  .how { left: 0; top: 1102px; width: 1200px; height: 548px; background: linear-gradient(180deg, #39b9ea 0%, #2cb3e7 50%, #33b8ea 100%); }
  .how-title { top: 68px; font-size: 32px; color: var(--white); }
  .video { left: 311px; top: 141px; width: 577px; height: 326px; border: 3px solid #e9eef1; background: linear-gradient(135deg, #8a8f93 0%, #6f7478 50%, #9a9ea0 100%); }
  .play { left: 255px; top: 131px; }

  /* Tutors */
  .tutors-title { top: 1695px; font-size: 34px; }
  .tutor { top: 1781px; width: 219px; }
  .tutor-photo { width: 219px; height: 204px; background: linear-gradient(180deg, #d9d9d9 0%, #c4c4c4 100%); }
  .tutor-body { height: 159px; color: var(--white); text-align: center; padding-top: 24px; }
  .tutor-body.green { background: var(--lime); }
  .tutor-body.blue { background: var(--sky); }
  .tutor-body h4 { font-family: "Lato", Arial, sans-serif; font-weight: 300; font-size: 19px; }
  .tutor-body p { margin: 14px auto 0; width: 185px; font-size: 10px; line-height: 20px; }

  /* Footer */
  .footer { left: 0; top: 2191px; width: 1200px; height: 240px; background: var(--footer); color: var(--white); }
  .footer .brand { left: 138px; top: 56px; }
  .footer-social { left: 131px; top: 122px; display: flex; gap: 7px; }
  .footer-social span { width: 31px; height: 31px; border-radius: 50%; border: 2px solid var(--white); display: block; }
  .footer-col h5 { font-family: "Lato", Arial, sans-serif; font-weight: 400; font-size: 14px; letter-spacing: .3px; }
  .quick-links { left: 424px; top: 52px; }
  .quick-links ul { list-style: none; margin-top: 16px; font-size: 10.5px; line-height: 19.3px; }
  .newsletter { left: 615px; top: 52px; width: 190px; }
  .newsletter p { margin-top: 16px; font-size: 10.5px; line-height: 19px; }
  .news-field { margin-top: 12px; width: 171px; height: 29px; background: var(--footer-field); font-size: 10px; padding: 8px 9px; }
  .news-btn { margin-top: 10px; width: 69px; height: 24px; background: var(--sky-dark); border-radius: 2px; font-size: 10px; display: flex; align-items: center; justify-content: center; }
  .contact { left: 887px; top: 52px; width: 190px; }
  .contact-row { display: flex; gap: 14px; align-items: flex-start; font-size: 10.5px; line-height: 19px; }
  .contact-row .dot { flex: none; width: 27px; height: 27px; border-radius: 50%; background: var(--footer-deep); display: flex; align-items: center; justify-content: center; }

  .bottombar { left: 0; top: 2431px; width: 1200px; height: 55px; background: var(--footer-deep); color: var(--white); font-size: 10.5px; }
  .copyright { left: 133px; top: 19px; }
  .payments { left: 958px; top: 19px; display: flex; gap: 5px; }
  .payments span { width: 23px; height: 15px; border-radius: 2px; display: block; }
</style>
</head>
<body>

  <div class="abs topbar">
    <div class="abs contact-item" style="left:133px">
      <svg width="10" height="10" viewBox="0 0 24 24"><path fill="#fff" d="M6.6 10.8a15 15 0 0 0 6.6 6.6l2.2-2.2a1 1 0 0 1 1-.25 11.4 11.4 0 0 0 3.6.57 1 1 0 0 1 1 1V20a1 1 0 0 1-1 1A17 17 0 0 1 3 4a1 1 0 0 1 1-1h3.5a1 1 0 0 1 1 1c0 1.25.2 2.45.57 3.57a1 1 0 0 1-.25 1z"/></svg>
      <span>1800 - 123 - 456</span>
    </div>
    <div class="abs contact-item" style="left:245px">
      <svg width="12" height="10" viewBox="0 0 24 20"><rect x="1" y="1" width="22" height="18" fill="none" stroke="#fff" stroke-width="2"/><path d="M1 2l11 9 11-9" fill="none" stroke="#fff" stroke-width="2"/></svg>
      <span>info@Yourmailid.com</span>
    </div>
    <div class="abs social"><span></span><span></span><span></span></div>
  </div>

  <header class="abs header">
    <div class="abs brand"><span class="brand-mark"></span><span class="brand-name">Brivora</span></div>
    <div class="abs auth-btn auth-register">REGISTER</div>
    <div class="abs auth-btn auth-login">LOGIN</div>
    <nav class="abs nav">
      <a class="active" style="left:585px">HOME</a>
      <a style="left:661px">ABOUT US</a>
      <a style="left:761px">SERVICES</a>
      <a style="left:861px">PRICING</a>
      <a style="left:951px">CONTACT US</a>
      <svg class="abs" style="left:1054px;top:1px" width="12" height="12" viewBox="0 0 24 24"><circle cx="10" cy="10" r="7" fill="none" stroke="#777" stroke-width="2.5"/><path d="M15 15l7 7" stroke="#777" stroke-width="2.5"/></svg>
    </nav>
    <div class="abs" style="left:580px;top:100px;width:50px;height:3px;background:var(--sky)"></div>
  </header>

  <section class="abs hero" role="img" aria-label="Photo of a student in a knitted hat working on a laptop">
    <h1 class="abs hero-title">ONLINE TRAINING</h1>
    <p class="abs hero-sub">End users of site are younger generation - tutees (8-18 years), tutors (19-25), parents (30-50)</p>
    <div class="abs hero-btn">READ MORE</div>
    <div class="abs hero-dots"><span class="current"></span><span></span><span></span></div>
  </section>

  <section class="welcome">
    <h2 class="abs section-title welcome-title">WELCOME TO BRIVORA</h2>
    <p class="abs welcome-intro">Nemo enim ipsam voluptatem quia voluptas sit aspernatur aut odit aut fugit, sed quia consequuntur magni dolores eos qui ratione voluptatem sequi nesciunt. Neque porro quisquam est, qui dolorem ipsum quia dolor sit amet, consectetur, adipisci velit, sed quia non numquam eius modi tempora incidunt ut labore et dolore magnam aliquam quaerat voluptatem.</p>

    <div class="abs feature" style="left:117px">
      <div class="feature-icon green">
        <svg width="34" height="24" viewBox="0 0 34 24"><rect x="0" y="2" width="22" height="20" rx="4" fill="#fff"/><path d="M23 9l11-7v20l-11-7z" fill="#fff"/></svg>
      </div>
      <h3>WEBCAM</h3>
      <p>Lorem ipsum dolor sit amet, consectetur adipiscing elit, sed do eiusmod tempor incididunt ut labore et dolore magna aliqua.</p>
      <div class="btn-small">Read More</div>
    </div>

    <div class="abs feature" style="left:450px">
      <div class="feature-icon blue">
        <svg width="36" height="30" viewBox="0 0 36 30"><ellipse cx="14" cy="11" rx="13" ry="10" fill="#fff"/><path d="M5 18l-3 8 9-5z" fill="#fff"/><ellipse cx="24" cy="17" rx="11" ry="8.5" fill="#fff" stroke="#29b6e8" stroke-width="2"/><path d="M30 23l4 6-9-4z" fill="#fff"/></svg>
      </div>
      <h3>INTERACTIVE</h3>
      <p>Lorem ipsum dolor sit amet, consectetur adipiscing elit, sed do eiusmod tempor incididunt ut labore et dolore magna aliqua.</p>
      <div class="btn-small">Read More</div>
    </div>

    <div class="abs feature" style="left:786px">
      <div class="feature-icon blue">
        <svg width="30" height="30" viewBox="0 0 30 30"><circle cx="15" cy="15" r="12" fill="none" stroke="#fff" stroke-width="3"/><path d="M15 8v8h6" fill="none" stroke="#fff" stroke-width="3"/></svg>
      </div>
      <h3>HOURLY</h3>
      <p>Lorem ipsum dolor sit amet, consectetur adipiscing elit, sed do eiusmod tempor incididunt ut labore et dolore magna aliqua.</p>
      <div class="btn-small">Read More</div>
    </div>
  </section>

  <section class="abs how">
    <h2 class="abs section-title how-title">HOW IT WORKS</h2>
    <div class="abs video" role="img" aria-label="Video still of three children sharing a laptop">
      <svg class="abs play" width="62" height="62" viewBox="0 0 62 62"><circle cx="31" cy="31" r="29" fill="#e6e6e6" opacity=".85" stroke="#555" stroke-width="3"/><path d="M24 18l20 13-20 13z" fill="#444"/></svg>
    </div>
  </section>

  <section class="tutors">
    <h2 class="abs section-title tutors-title">TUTOR PROFILES</h2>
    <article class="abs tutor" style="left:133px">
      <div class="tutor-photo" role="img" aria-label="Portrait photo of a tutor"></div>
      <div class="tutor-body green"><h4>John Doe</h4><p>Lorem ipsum dolor sit amet, consectetur adipiscing elit, sed do eiusmod tempor incididunt</p></div>
    </article>
    <article class="abs tutor" style="left:372px">
      <div class="tutor-photo" role="img" aria-label="Portrait photo of a tutor"></div>
      <div class="tutor-body blue"><h4>John Doe</h4><p>Lorem ipsum dolor sit amet, consectetur adipiscing elit, sed do eiusmod tempor incididunt</p></div>
    </article>
    <article class="abs tutor" style="left:609px">
      <div class="tutor-photo" role="img" aria-label="Portrait photo of a tutor"></div>
      <div class="tutor-body blue"><h4>John Doe</h4><p>Lorem ipsum dolor sit amet, consectetur adipiscing elit, sed do eiusmod tempor incididunt</p></div>
    </article>
    <article class="abs tutor" style="left:848px">
      <div class="tutor-photo" role="img" aria-label="Portrait photo of a tutor"></div>
      <div class="tutor-body blue"><h4>John Doe</h4><p>Lorem ipsum dolor sit amet, consectetur adipiscing elit, sed do eiusmod tempor incididunt</p></div>
    </article>
  </section>

  <footer class="abs footer">
    <div class="abs brand"><span class="brand-mark"></span><span class="brand-name">Brivora</span></div>
    <div class="abs footer-social"><span></span><span></span><span></span><span></span><span></span></div>

    <div class="abs footer-col quick-links">
      <h5>QUICK LINKS</h5>
      <ul><li>Home</li><li>About Us</li><li>Services</li><li>Pricing</li><li>Blog</li><li>Contact Us</li></ul>
    </div>

    <div class="abs footer-col newsletter">
      <h5>NEWSLETTER</h5>
      <p>Subscribe newsletter to receive the updates direct to your inbox.</p>
      <div class="news-field">Enter Email Id</div>
      <div class="news-btn">Subscribe</div>
    </div>

    <div class="abs footer-col contact">
      <h5>CONTACT US</h5>
      <div class="contact-row" style="margin-top:16px">
        <span class="dot"><svg width="10" height="12" viewBox="0 0 20 26"><path d="M10 0a9 9 0 0 0-9 9c0 7 9 17 9 17s9-10 9-17a9 9 0 0 0-9-9z" fill="#fff"/><circle cx="10" cy="9" r="3.5" fill="#3c474f"/></svg></span>
        <span>Lorem ipsum dolor sit amet, consectetur</span>
      </div>
      <div class="contact-row" style="margin-top:8px">
        <span class="dot"><svg width="11" height="11" viewBox="0 0 24 24"><path fill="#fff" d="M6.6 10.8a15 15 0 0 0 6.6 6.6l2.2-2.2a1 1 0 0 1 1-.25 11.4 11.4 0 0 0 3.6.57 1 1 0 0 1 1 1V20a1 1 0 0 1-1 1A17 17 0 0 1 3 4a1 1 0 0 1 1-1h3.5a1 1 0 0 1 1 1c0 1.25.2 2.45.57 3.57a1 1 0 0 1-.25 1z"/></svg></span>
        <span style="padding-top:4px">1800-123-4567</span>
      </div>
      <div class="contact-row" style="margin-top:10px">
        <span class="dot"><svg width="12" height="9" viewBox="0 0 24 18"><rect width="24" height="18" fill="#fff"/><path d="M0 1l12 9 12-9" fill="none" stroke="#3c474f" stroke-width="2"/></svg></span>
        <span style="padding-top:4px">info@yourmailid.com</span>
      </div>
    </div>
  </footer>

  <div class="abs bottombar">
    <div class="abs copyright">Copyright © 2016 brivora.com.au &nbsp;| All Rights Reserved</div>
    <div class="abs payments">
      <span style="background:#e8912b"></span>
      <span style="background:#2f7fd0"></span>
      <span style="background:#e0a03a"></span>
      <span style="background:#3a8fd8"></span>
    </div>
  </div>

</body>
</html>
```